Copper Field Agency Website - Wordpress Web UPDATED BRIEF

FINAL LOGO UPLOADED - please look to this as reference for how we would like the site to look and feel.

We are a digital marketing agency - looking to have a new website built. We are looking for a simple one page feel of site that will allow us to grow it later. (Feel free to take some liberties with that if your imagination veers off) Must be very, playful, bold, sleek and easily integrate video. Wordpress only.

Overview:

Copper Field is a creative constellation. We are built on what's great about the shared economy. With access to thousands of content creators, designers, technicians, writers, strategists and other creatives around the world, we are built differently than a traditional “brick and mortar” Marketing Agency. We provide the traditional services our clients have come to expect, without the “5X factor” of covering the overhead common in the old agency model. We believe even better work can be created in collaboration with our clients and by passing those savings back to them for their use. Our clients pay for our art, our work and our passion –not our furniture.

"Copper Field, Let's Build Together"

Target Market(s)

companies looking for creative agency help, video production, creative consulting and coaching

Industry/Entity Type

Digital Marketing

Coding

Coded - Design and coding required

Number of Pages Required

1 page

Font styles to use
Sans Serif

Colors
3277b5
33a6d7
ec1f27

Requirements
Must have
• Wordpress design is a must. Looking for a one sheet homepage - with sections that are all on the main front page. We will have videos to embed, and should be able to have client logos and easy access to show a variety of our creative work.
• Please look to the logo for how we would like the site to feel.
• Please think "icon process flow" instead of blocks of text (which we used to have). Use the text to explain what the process flow should represent - don't actually copy paste the text but show it visually in icons.
Nice to have
• innovation around how we show video content. solid colors complementary to our palette and aesthetic.
Should not have
• Standard HTML coding

```html
<!DOCTYPE html>
<html lang="en">
<head>
<meta charset="utf-8">
<title>Copper Field Agency</title>
<link href="https://fonts.googleapis.com/css2?family=Roboto+Condensed:wght@400;700&family=Roboto:wght@400;500;700&display=swap" rel="stylesheet">
<style>
:root{
  --red:#ec1f27;
  --blue:#3277b5;
  --sky:#33a6d7;
  --services:#2e8fd2;
  --ink:#1b1b1b;
  --white:#ffffff;
  --grey:#8a8a8a;
  --black:#0c0c0c;
}
*{box-sizing:border-box;margin:0;padding:0}
html,body{width:1200px;height:4480px;overflow:hidden}
body{font-family:"Roboto",Arial,sans-serif;color:var(--ink);background:var(--white);position:relative}
.section{position:absolute;left:0;width:1200px;overflow:hidden}
.heading{position:absolute;left:0;width:100%;text-align:center;font-family:"Roboto Condensed",Arial,sans-serif;font-weight:700;font-size:40px;letter-spacing:1px;text-transform:uppercase}
.fill{position:absolute}

/* hero */
.hero{top:0;height:660px}
.hero-photo{inset:0;background:linear-gradient(100deg,#d9d6d4 0%,#b9b4b3 30%,#e4e4e6 55%,#f1f1f2 100%)}
.hero-cubes{left:560px;top:110px;width:520px;height:520px;background:radial-gradient(circle at 50% 45%,#4aa6d6 0%,#c7c9cd 38%,#d8262e 62%,rgba(230,230,232,0) 75%)}
.nav{position:absolute;top:44px;left:268px;display:flex;gap:28px;font-size:14px;font-weight:500;color:var(--white);text-transform:uppercase;letter-spacing:.5px}
.social{position:absolute;display:flex;gap:16px}
.social span{width:14px;height:14px;border-radius:50%;background:var(--white);display:block}
.header-social{top:46px;left:990px}
.brand{position:absolute;left:40px;top:20px;display:flex;align-items:center;gap:12px}
.brand-dot{width:70px;height:70px;border-radius:50%;background:var(--blue)}
.brand-name{font-family:"Roboto Condensed",Arial,sans-serif;font-weight:700;font-size:26px;color:var(--red);text-transform:uppercase;line-height:1.05;width:110px}
.hero-title{position:absolute;left:144px;top:328px;font-family:"Roboto Condensed",Arial,sans-serif;font-weight:700;font-size:40px;color:var(--white);text-transform:uppercase;letter-spacing:1px}
.hero-text{position:absolute;left:144px;top:384px;width:420px;font-size:17px;line-height:1.4;color:var(--white)}
.btn-outline{position:absolute;left:144px;top:488px;padding:8px 22px;border:2px solid var(--red);border-radius:20px;background:var(--white);color:var(--red);font-size:14px;font-weight:700;text-transform:uppercase}
.hero-arrow{position:absolute;top:378px}
.hero-dots{position:absolute;top:612px;left:560px;display:flex;gap:10px}
.hero-dots span{width:10px;height:10px;border-radius:50%;background:var(--white);opacity:.6}
.hero-dots span:first-child{opacity:1}

/* videos */
.videos{top:660px;height:480px;background:#f2f2f2}
.videos .heading{top:76px}
.video-card{position:absolute;top:152px;width:324px}
.video-thumb{position:relative;height:208px;background:linear-gradient(135deg,#2f3640,#6b5a4c)}
.video-thumb .play{position:absolute;left:50%;top:50%;transform:translate(-50%,-50%)}
.video-caption{margin-top:26px;font-size:14px;font-weight:700;line-height:1.45;text-transform:uppercase}

/* services */
.services{top:1140px;height:680px;background:var(--services)}
.services .heading{top:90px;color:var(--white)}
.service{position:absolute;width:240px;text-align:center;color:var(--white)}
.service svg{display:block;margin:0 auto 18px}
.service-label{font-size:19px;font-weight:500;text-transform:uppercase;line-height:1.25}

/* gallery */
.gallery{top:1820px;height:692px}
.gallery-bg{inset:0;background:linear-gradient(160deg,#1f4f86 0%,#2f6ea6 45%,#1a3658 100%)}
.gallery .heading{top:132px;color:var(--white)}
.gallery-item{position:absolute;top:244px;width:356px;height:256px}
.gallery-arrow{position:absolute;top:354px;width:34px;height:34px;background:var(--red);display:flex;align-items:center;justify-content:center}

/* clients */
.clients{top:2512px;height:128px;background:var(--black)}
.client-list{position:absolute;left:140px;top:0;width:920px;height:128px;display:flex;align-items:center;justify-content:space-between}
.client{font-size:17px;font-weight:500;color:#b9b9b9;text-transform:uppercase;letter-spacing:.5px}
.client-arrow{position:absolute;top:48px;width:32px;height:32px;background:var(--red);display:flex;align-items:center;justify-content:center}

/* testimonials */
.testimonials{top:2640px;height:560px;background:var(--white)}
.testimonials .heading{top:72px}
.testimonial{position:absolute;top:172px;width:512px;height:252px;border:2px solid var(--red)}
.avatar{position:absolute;left:60px;top:64px;width:100px;height:100px;border-radius:50%;background:linear-gradient(135deg,#e8cdb8,#b88a6a)}
.stars{position:absolute;left:196px;top:40px;display:flex;gap:4px}
.quote-text{position:absolute;left:196px;top:72px;width:220px;font-size:13px;line-height:1.5;color:#444}
.quote-name{position:absolute;left:196px;top:168px;font-size:14px;font-weight:700}
.quote-mark{position:absolute;right:24px;top:60px;font-family:"Roboto",Arial,sans-serif;font-weight:700;font-size:200px;line-height:1;color:#e3e3e3}
.pager{position:absolute;top:484px;left:552px;display:flex;gap:12px}
.pager span{width:36px;height:36px;border-radius:50%;display:flex;align-items:center;justify-content:center}

/* join */
.join{top:3200px;height:600px}
.join-bg{inset:0;background:linear-gradient(180deg,#d8141c 0%,#ec1f27 55%,#c8141b 100%)}
.join .heading{top:48px;color:var(--white)}
.field{position:absolute;border:1.5px solid rgba(255,255,255,.85);color:var(--white);font-size:14px;padding:10px 14px}
.submit{position:absolute;left:460px;top:420px;width:200px;height:52px;background:var(--black);color:var(--white);font-size:16px;font-weight:500;text-transform:uppercase;display:flex;align-items:center;justify-content:center}

/* contact */
.contact{top:3800px;height:500px}
.contact-map{inset:0;background:linear-gradient(150deg,#cfe3d2 0%,#e9eee3 40%,#bcd8e8 75%,#a9cde0 100%)}
.contact .heading{top:40px;color:var(--ink)}
.contact-item{position:absolute;top:276px;width:360px;text-align:center}
.contact-item svg{display:block;margin:0 auto 10px}
.contact-label{font-size:20px;font-weight:700;color:var(--red);text-transform:uppercase}
.contact-value{margin-top:8px;font-size:20px;font-weight:500;color:var(--ink);text-transform:uppercase;line-height:1.3}

/* footer */
.footer{top:4300px;height:180px;background:var(--black);color:var(--white)}
.footer-nav{position:absolute;top:28px;left:0;width:100%;display:flex;justify-content:center;gap:28px;font-size:13px;text-transform:uppercase}
.footer-social{top:80px;left:540px}
.copyright{position:absolute;top:120px;width:100%;text-align:center;font-size:13px;color:#cfcfcf}
</style>
</head>
<body>

<header class="section hero">
  <div class="fill hero-photo" role="img" aria-label="Photo of a smiling woman working in a bright office"></div>
  <div class="fill hero-cubes" role="img" aria-label="Illustration of red, blue and grey cubes forming a large cube with a video play button"></div>
  <div class="brand"><span class="brand-dot"></span><span class="brand-name">Copper Field</span></div>
  <nav class="nav"><span>Home</span><span>Videos</span><span>Services</span><span>Gallery</span><span>Clients</span><span>Testimonials</span><span>Contact Us</span></nav>
  <div class="social header-social" aria-label="Social links"><span></span><span></span><span></span><span></span></div>
  <svg class="hero-arrow" style="left:60px" width="24" height="32" viewBox="0 0 24 32"><path d="M18 4 6 16l12 12" fill="none" stroke="#fff" stroke-width="4"/></svg>
  <svg class="hero-arrow" style="right:60px" width="24" height="32" viewBox="0 0 24 32"><path d="M6 4l12 12L6 28" fill="none" stroke="#222" stroke-width="4"/></svg>
  <h1 class="hero-title">Copper Field</h1>
  <p class="hero-text">Sed ut perspiciatis unde omnis iste natus error sit voluptatem accusantium</p>
  <span class="btn-outline">Read More</span>
  <div class="hero-dots"><span></span><span></span><span></span></div>
</header>

<section class="section videos">
  <h2 class="heading">Videos</h2>
  <div class="video-card" style="left:72px">
    <div class="video-thumb" role="img" aria-label="Video still of a person holding a sign against a brick wall">
      <svg class="play" width="56" height="40" viewBox="0 0 56 40"><rect width="56" height="40" rx="9" fill="#ec1f27"/><path d="M22 11l14 9-14 9z" fill="#fff"/></svg>
    </div>
    <p class="video-caption">Sed ut perspiciatis unde omnis iste<br>natus error sit voluptatem</p>
  </div>
  <div class="video-card" style="left:436px">
    <div class="video-thumb" role="img" aria-label="Video still of hands on a laptop with digital marketing graphics">
      <svg class="play" width="56" height="40" viewBox="0 0 56 40"><rect width="56" height="40" rx="9" fill="#ec1f27"/><path d="M22 11l14 9-14 9z" fill="#fff"/></svg>
    </div>
    <p class="video-caption">Sed ut perspiciatis unde omnis iste<br>natus error sit voluptatem</p>
  </div>
  <div class="video-card" style="left:800px">
    <div class="video-thumb" role="img" aria-label="Video still of a laptop on a wooden desk">
      <svg class="play" width="56" height="40" viewBox="0 0 56 40"><rect width="56" height="40" rx="9" fill="#ec1f27"/><path d="M22 11l14 9-14 9z" fill="#fff"/></svg>
    </div>
    <p class="video-caption">Sed ut perspiciatis unde omnis iste<br>natus error sit voluptatem</p>
  </div>
</section>

<section class="section services">
  <h2 class="heading">Services</h2>
  <div class="service" style="left:120px;top:180px">
    <svg width="80" height="80" viewBox="0 0 80 80" fill="none" stroke="#fff" stroke-width="2.5"><circle cx="40" cy="36" r="22"/><path d="M18 36h44M40 14c-9 10-9 34 0 44M40 14c9 10 9 34 0 44M30 70h20M40 58v12"/></svg>
    <div class="service-label">Discovery</div>
  </div>
  <div class="service" style="left:480px;top:180px">
    <svg width="80" height="80" viewBox="0 0 80 80" fill="none" stroke="#fff" stroke-width="2.5"><path d="M14 14h20v8a6 6 0 1 0 12 0v-8h20v20h-8a6 6 0 1 0 0 12h8v20H46v-8a6 6 0 1 0-12 0v8H14V46h8a6 6 0 1 0 0-12h-8z"/></svg>
    <div class="service-label">Strategy</div>
  </div>
  <div class="service" style="left:840px;top:180px">
    <svg width="80" height="80" viewBox="0 0 80 80" fill="none" stroke="#fff" stroke-width="2.5"><rect x="12" y="16" width="36" height="48" rx="3"/><rect x="32" y="10" width="36" height="48" rx="3"/><path d="M40 24h20M40 32h20M40 40h14"/><circle cx="24" cy="50" r="6"/></svg>
    <div class="service-label">Project<br>Management</div>
  </div>
  <div class="service" style="left:120px;top:420px">
    <svg width="80" height="80" viewBox="0 0 80 80" fill="none" stroke="#fff" stroke-width="2.5"><rect x="14" y="10" width="30" height="22" rx="2"/><path d="M44 40V26a4 4 0 0 1 8 0v16l10 2a5 5 0 0 1 4 6l-3 18H42L32 52a4 4 0 0 1 6-5l6 5"/></svg>
    <div class="service-label">Content</div>
  </div>
  <div class="service" style="left:480px;top:420px">
    <svg width="80" height="80" viewBox="0 0 80 80" fill="none" stroke="#fff" stroke-width="2.5"><circle cx="32" cy="44" r="10"/><path d="M32 24v6M32 58v6M12 44h6M46 44h6M18 30l4 4M42 54l4 4M18 58l4-4M42 34l4-4"/><circle cx="58" cy="22" r="6"/><path d="M58 10v4M58 30v4M46 22h4M66 22h4"/></svg>
    <div class="service-label">Production</div>
  </div>
  <div class="service" style="left:840px;top:420px">
    <svg width="80" height="80" viewBox="0 0 80 80" fill="none" stroke="#fff" stroke-width="2.5"><circle cx="40" cy="40" r="10"/><path d="M22 70c2-12 10-18 18-18s16 6 18 18"/><rect x="8" y="10" width="22" height="16" rx="2"/><rect x="50" y="10" width="22" height="16" rx="2"/><path d="M56 18h10M14 18h10"/></svg>
    <div class="service-label">Paid Media<br>and Coaching</div>
  </div>
</section>

<section class="section gallery">
  <div class="fill gallery-bg" role="img" aria-label="Photo of people working at laptops, tinted blue"></div>
  <h2 class="heading">Gallery</h2>
  <div class="fill gallery-item" style="left:72px;background:linear-gradient(135deg,#f4f6f8,#9fc3e6 60%,#2a69b8)" role="img" aria-label="Abstract blue geometric frame"></div>
  <div class="fill gallery-item" style="left:438px;background:linear-gradient(135deg,#2f4c66,#7c99b0)" role="img" aria-label="Office desk with digital marketing graphics"></div>
  <div class="fill gallery-item" style="left:804px;background:linear-gradient(135deg,#d9c7a4,#6d7f8e)" role="img" aria-label="Hands working on a laptop with charts"></div>
  <span class="gallery-arrow" style="left:72px"><svg width="12" height="14" viewBox="0 0 12 14"><path d="M10 1 2 7l8 6z" fill="#fff"/></svg></span>
</section>

<section class="section clients">
  <span class="client-arrow" style="left:72px"><svg width="12" height="14" viewBox="0 0 12 14"><path d="M10 1 2 7l8 6z" fill="#fff"/></svg></span>
  <div class="client-list">
    <span class="client">Portbay</span>
    <span class="client">Alderwick</span>
    <span class="client">Lumenreach</span>
    <span class="client">Harlow &amp; Reed</span>
    <span class="client">Quillhaven</span>
    <span class="client">Northmere Goods</span>
  </div>
  <span class="client-arrow" style="right:72px"><svg width="12" height="14" viewBox="0 0 12 14"><path d="M2 1l8 6-8 6z" fill="#fff"/></svg></span>
</section>

<section class="section testimonials">
  <h2 class="heading">Tstimonials</h2>
  <article class="testimonial" style="left:72px">
    <div class="avatar" role="img" aria-label="Portrait of a client"></div>
    <div class="stars">
      <svg width="18" height="18" viewBox="0 0 20 20"><path d="M10 1l2.6 6 6.4.5-4.9 4.2 1.5 6.3L10 14.6 4.4 18l1.5-6.3L1 7.5 7.4 7z" fill="#ec1f27"/></svg>
      <svg width="18" height="18" viewBox="0 0 20 20"><path d="M10 1l2.6 6 6.4.5-4.9 4.2 1.5 6.3L10 14.6 4.4 18l1.5-6.3L1 7.5 7.4 7z" fill="#ec1f27"/></svg>
      <svg width="18" height="18" viewBox="0 0 20 20"><path d="M10 1l2.6 6 6.4.5-4.9 4.2 1.5 6.3L10 14.6 4.4 18l1.5-6.3L1 7.5 7.4 7z" fill="#ec1f27"/></svg>
      <svg width="18" height="18" viewBox="0 0 20 20"><path d="M10 1l2.6 6 6.4.5-4.9 4.2 1.5 6.3L10 14.6 4.4 18l1.5-6.3L1 7.5 7.4 7z" fill="#ec1f27"/></svg>
      <svg width="18" height="18" viewBox="0 0 20 20"><path d="M10 1l2.6 6 6.4.5-4.9 4.2 1.5 6.3L10 14.6 4.4 18l1.5-6.3L1 7.5 7.4 7z" fill="#ccc"/></svg>
    </div>
    <p class="quote-text">"Duis aute irure dolor in reprehenderit in voluptate velit esse cillum dolore eu fugiat nulla pariatur."</p>
    <p class="quote-name">- Marla</p>
    <span class="quote-mark">&#8221;</span>
  </article>
  <article class="testimonial" style="left:616px">
    <div class="avatar" role="img" aria-label="Portrait of a client"></div>
    <div class="stars">
      <svg width="18" height="18" viewBox="0 0 20 20"><path d="M10 1l2.6 6 6.4.5-4.9 4.2 1.5 6.3L10 14.6 4.4 18l1.5-6.3L1 7.5 7.4 7z" fill="#ec1f27"/></svg>
      <svg width="18" height="18" viewBox="0 0 20 20"><path d="M10 1l2.6 6 6.4.5-4.9 4.2 1.5 6.3L10 14.6 4.4 18l1.5-6.3L1 7.5 7.4 7z" fill="#ec1f27"/></svg>
      <svg width="18" height="18" viewBox="0 0 20 20"><path d="M10 1l2.6 6 6.4.5-4.9 4.2 1.5 6.3L10 14.6 4.4 18l1.5-6.3L1 7.5 7.4 7z" fill="#ec1f27"/></svg>
      <svg width="18" height="18" viewBox="0 0 20 20"><path d="M10 1l2.6 6 6.4.5-4.9 4.2 1.5 6.3L10 14.6 4.4 18l1.5-6.3L1 7.5 7.4 7z" fill="#ec1f27"/></svg>
      <svg width="18" height="18" viewBox="0 0 20 20"><path d="M10 1l2.6 6 6.4.5-4.9 4.2 1.5 6.3L10 14.6 4.4 18l1.5-6.3L1 7.5 7.4 7z" fill="#ccc"/></svg>
    </div>
    <p class="quote-text">"Duis aute irure dolor in reprehenderit in voluptate velit esse cillum dolore eu fugiat nulla pariatur."</p>
    <p class="quote-name">- Marla</p>
    <span class="quote-mark">&#8221;</span>
  </article>
  <div class="pager">
    <span style="background:var(--red)"><svg width="10" height="12" viewBox="0 0 10 12"><path d="M8 1 2 6l6 5" fill="none" stroke="#fff" stroke-width="2"/></svg></span>
    <span style="background:#e6e6e6"><svg width="10" height="12" viewBox="0 0 10 12"><path d="M2 1l6 5-6 5" fill="none" stroke="#333" stroke-width="2"/></svg></span>
  </div>
</section>

<section class="section join">
  <div class="fill join-bg" role="img" aria-label="Red-tinted brick wall with digital marketing graphics"></div>
  <h2 class="heading">Join Us</h2>
  <div class="field" style="left:120px;top:136px;width:432px;height:48px">First Name</div>
  <div class="field" style="left:580px;top:136px;width:428px;height:48px">Last Name</div>
  <div class="field" style="left:120px;top:208px;width:432px;height:48px">Email address</div>
  <div class="field" style="left:580px;top:208px;width:428px;height:48px">Phone Number</div>
  <div class="field" style="left:120px;top:280px;width:888px;height:120px">Type Message</div>
  <div class="submit">Submit</div>
</section>

<section class="section contact">
  <div class="fill contact-map" role="img" aria-label="Map of the Caribbean region"></div>
  <h2 class="heading">Contact Us</h2>
  <div class="contact-item" style="left:40px">
    <svg width="44" height="56" viewBox="0 0 44 56"><path d="M22 3C12 3 5 10 5 20c0 13 17 32 17 32s17-19 17-32C39 10 32 3 22 3z" fill="none" stroke="#ec1f27" stroke-width="3"/><circle cx="22" cy="20" r="6" fill="none" stroke="#ec1f27" stroke-width="3"/></svg>
    <div class="contact-label">Address</div>
    <div class="contact-value">245 Orchard Lane #4B<br>Denton TX 76201</div>
  </div>
  <div class="contact-item" style="left:420px">
    <svg width="52" height="56" viewBox="0 0 52 56"><path d="M14 6l8 10-5 6c3 7 8 12 15 16l6-5 10 8-5 9C22 50 4 30 6 12z" fill="none" stroke="#ec1f27" stroke-width="3" stroke-linejoin="round"/></svg>
    <div class="contact-label">Phone</div>
    <div class="contact-value">555.214.7780</div>
  </div>
  <div class="contact-item" style="left:800px">
    <svg width="56" height="56" viewBox="0 0 56 56"><rect x="4" y="12" width="48" height="34" fill="none" stroke="#ec1f27" stroke-width="3"/><path d="M4 12l24 20 24-20" fill="none" stroke="#ec1f27" stroke-width="3"/></svg>
    <div class="contact-label">Email</div>
    <div class="contact-value">hello@copperfield.example</div>
  </div>
</section>

<footer class="section footer">
  <nav class="footer-nav"><span>Home</span><span>Videos</span><span>Services</span><span>Gallery</span><span>Clients</span><span>Testimonials</span><span>Contact Us</span></nav>
  <div class="social footer-social" aria-label="Social links"><span></span><span></span><span></span><span></span><span></span></div>
  <p class="copyright">&copy; 2019 | www.copperfield.example</p>
</footer>

</body>
</html>
```